Brandwyn Fuel Retro Website Design

Have a logo. Need a website design to go along with the logo design. Full Design Specs are here: https://files.plinverdocs.net/sheet/d/8QmRtZxWv3-41pk527LNB_XY4HaPcOdsuw2K-rb6/view

Target Market(s)

Independent Gas Station Owners

Number of Pages Required

1 page

Font styles to use
Sans Serif

Colors

Designer to choose colors to be used in the design.

```html
<!DOCTYPE html>
<html lang="en">
<head>
<meta charset="utf-8">
<title>Brandwyn Fuel</title>
<link href="https://fonts.googleapis.com/css2?family=Alfa+Slab+One&family=Lato:wght@400;700&display=swap" rel="stylesheet">
<style>
:root{
  --red:#e3232d;
  --red-dark:#b51a22;
  --ink:#3b3b3d;
  --charcoal:#404042;
  --charcoal-deep:#2e2e30;
  --paper:#e7e7e7;
  --white:#ffffff;
  --text:#444446;
  --muted:#5a5a5c;
}
*{margin:0;padding:0;box-sizing:border-box}
html,body{width:1200px;height:2844px;overflow:hidden}
body{position:relative;font-family:"Lato",sans-serif;color:var(--text);background:var(--white)}
.abs{position:absolute}
.display{font-family:"Alfa Slab One",serif;font-weight:400;letter-spacing:.5px}

/* header */
.topbar{left:0;top:0;width:1200px;height:62px;background:var(--charcoal)}
.navbar{left:0;top:62px;width:1200px;height:53px;background:var(--red)}
.nav-link{top:62px;height:53px;line-height:53px;color:var(--white);font-size:13.5px;text-transform:uppercase;text-decoration:none}
.nav-link.active{color:#f6b6ba}
.brand-tab{left:517px;top:20px;width:166px;height:140px;background:var(--red);border-radius:48px 48px 28px 28px;display:flex;flex-direction:column;align-items:center;justify-content:center;gap:12px;z-index:10}
.brand-dot{width:50px;height:50px;border-radius:50%;background:var(--white)}
.brand-name{color:var(--white);font-weight:700;font-size:15px;text-transform:uppercase;letter-spacing:1px;white-space:nowrap;line-height:1}

/* hero */
.hero{left:0;top:115px;width:1200px;height:625px;background:linear-gradient(180deg,#cfcbc0 0%,#bdb8ab 45%,#8e897d 80%,#5f5b53 100%)}
.hero-ribbon{left:480px;top:238px;width:240px;height:62px;background:#eeece6;display:flex;align-items:center;justify-content:center;color:var(--ink);font-size:24px}
.hero-title{left:0;top:335px;width:1200px;text-align:center;color:#f3f1ec;font-size:78px;text-shadow:3px 4px 0 var(--red-dark);letter-spacing:2px}

/* welcome */
.welcome{left:0;top:740px;width:1200px;height:687px;background:var(--paper)}
.section-title{color:var(--red);text-align:center;text-transform:uppercase}
.lead{left:240px;top:860px;width:720px;text-align:center;font-size:18.5px;line-height:29px;color:var(--ink)}
.body-copy{left:230px;top:970px;width:740px;text-align:center;font-size:14px;line-height:25px;color:var(--ink)}
.btn{display:flex;align-items:center;justify-content:center;color:var(--white);font-family:"Alfa Slab One",serif;font-size:17px;text-transform:uppercase;box-shadow:4px 4px 0 #f08a90}
.btn-red{background:var(--red)}
.btn-dark{background:var(--charcoal);box-shadow:4px 4px 0 #6e6e70}
.rule{left:77px;top:1207px;width:1047px;height:2px;background:#d4d4d4}

/* services */
.service-photo{width:146px;height:146px;border-radius:50%;border:4px solid var(--red);background:radial-gradient(circle at 45% 40%,#b9b9b9,#6d6d6d)}
.service-name{width:250px;text-align:center;color:var(--red);font-size:20px;text-transform:uppercase;top:1524px}
.service-text{width:236px;text-align:center;top:1560px;font-size:14px;line-height:25px;color:var(--muted)}
.read-more{width:250px;text-align:center;top:1650px;color:var(--red);font-family:"Alfa Slab One",serif;font-size:16px;text-decoration:underline;text-transform:uppercase}

/* containers */
.photo-frame{left:77px;top:1810px;width:510px;height:354px;background:var(--white);box-shadow:0 2px 14px rgba(0,0,0,.18)}
.photo-fill{left:87px;top:1821px;width:489px;height:332px;background:linear-gradient(180deg,#e4e4e4 0%,#a9a9a9 55%,#7c7c7c 100%)}
.feature-title{left:683px;top:1845px;color:var(--red);font-size:38px;text-transform:uppercase}
.feature-copy{left:683px;width:420px;font-size:14px;line-height:25px;color:var(--ink)}

/* careers */
.careers{left:0;top:2261px;width:1200px;height:218px;background:var(--red)}
.careers-title{left:80px;top:2312px;color:var(--white);font-size:35px;text-transform:uppercase}
.careers-copy{left:79px;top:2369px;width:700px;color:var(--white);font-size:16.5px;line-height:27px}

/* footer */
.footer{left:0;top:2479px;width:1200px;height:302px;background:var(--charcoal)}
.footer-title{color:var(--white);font-size:23px;text-transform:uppercase;top:2540px}
.sitemap-link{color:#e2e2e2;font-size:14px}
.sitemap-link::before{content:"";position:absolute;left:-17px;top:5px;width:8px;height:8px;border-radius:50%;background:var(--red)}
.footer-brand{left:496px;top:2536px;width:200px;display:flex;flex-direction:column;align-items:center;gap:14px}
.footer-brand .brand-dot{width:110px;height:110px;background:var(--red);border:5px solid var(--white)}
.footer-brand .brand-name{font-size:20px}
.contact-line{left:874px;width:250px;color:#e2e2e2;font-size:14px;line-height:26px}
.contact-icon{left:842px;width:18px;height:18px}
.copyright-bar{left:0;top:2781px;width:1200px;height:63px;background:var(--charcoal-deep);color:#dcdcdc;font-size:14px;display:flex;align-items:center;justify-content:center}
</style>
</head>
<body>

<section>
  <div class="abs hero" role="img" aria-label="Vintage sepia photograph of a fuel company depot with old tanker trucks, workers and storage tanks"></div>
  <div class="abs hero-ribbon display">EST 1966</div>
  <h1 class="abs hero-title display">CULINARY CENTER</h1>
</section>

<header>
  <div class="abs topbar"></div>
  <nav class="abs navbar"></nav>
  <a class="abs nav-link active" style="left:207px">Home</a>
  <a class="abs nav-link" style="left:287px">About Us</a>
  <a class="abs nav-link" style="left:391px">Services</a>
  <a class="abs nav-link" style="left:748px">Containers</a>
  <a class="abs nav-link" style="left:870px">Career</a>
  <a class="abs nav-link" style="left:958px">Contact</a>
  <div class="abs brand-tab">
    <span class="brand-dot"></span>
    <span class="brand-name">Brandwyn Fuel</span>
  </div>
</header>

<section>
  <div class="abs welcome"></div>
  <h2 class="abs section-title display" style="left:0;top:795px;width:1200px;font-size:36px">Welcome to Brandwyn Fuel</h2>
  <p class="abs lead">Lorem ipsum dolor sit amet, consectetur adipiscing elit, sed do eiusmod tempor incididunt ut labore et dolore magna aliqua. Ut enim ad minim veniam, quis nostrud exercitation ullamco laboris nisi ut aliquip ex ea commodo consequat.</p>
  <p class="abs body-copy">Lorem ipsum dolor sit amet, consectetur adipiscing elit, sed do eiusmod tempor incididunt ut labore et dolore magna aliqua. Ut enim ad minim veniam, quis nostrud exercitation ullamco laboris nisi ut aliquip ex ea commodo consequat. Duis aute irure dolor in reprehenderit in voluptate velit esse cillum dolore eu fugiat nulla pariatur.</p>
  <a class="abs btn btn-red" style="left:511px;top:1077px;width:178px;height:52px">Learn More</a>
  <div class="abs rule"></div>
</section>

<section>
  <h2 class="abs section-title display" style="left:0;top:1264px;width:1200px;font-size:36px">Our Services</h2>

  <div class="abs service-photo" style="left:124px;top:1352px" role="img" aria-label="Photo of a fuel delivery truck"></div>
  <h3 class="abs service-name display" style="left:72px">Fuel Delivery</h3>
  <p class="abs service-text" style="left:79px">Brandwyn Fuel provides fuel delivery for independent gas stations, convenience stores, construction...</p>
  <a class="abs read-more" style="left:72px">Read More</a>

  <div class="abs service-photo" style="left:392px;top:1352px" role="img" aria-label="Photo of shelves stocked with oil and lubricants"></div>
  <h3 class="abs service-name display" style="left:340px">Oil</h3>
  <p class="abs service-text" style="left:347px">Looking for speciality auto, tractor, tractor trailer, aviation or other commercial oils and lubricants...</p>
  <a class="abs read-more" style="left:340px">Read More</a>

  <div class="abs service-photo" style="left:661px;top:1352px" role="img" aria-label="Photo of farm fuel storage tanks"></div>
  <h3 class="abs service-name display" style="left:609px">Farm Fuel</h3>
  <p class="abs service-text" style="left:616px">Looking for gasoline, diesel red diesel off road fuel or farm diesel? We can deliver straight to your...</p>
  <a class="abs read-more" style="left:609px">Read More</a>

  <div class="abs service-photo" style="left:929px;top:1352px" role="img" aria-label="Photo of a cargo container's doors"></div>
  <h3 class="abs service-name display" style="left:877px">Cargo Containers</h3>
  <p class="abs service-text" style="left:884px">ant to purchase or lease a storage container, we have what you need! We can deliver or move storage...</p>
  <a class="abs read-more" style="left:877px">Read More</a>
</section>

<section>
  <div class="abs photo-frame"></div>
  <div class="abs photo-fill" role="img" aria-label="Black and white photo of a steel shipping container on gravel"></div>
  <h2 class="abs feature-title display">Containers</h2>
  <p class="abs feature-copy" style="top:1902px">Lorem ipsum dolor sit amet, consectetur adipiscing elit, sed do eiusmod tempor incididunt ut labore et dolore magna aliqua. Ut enim ad minim veniam, quis nostrud exercitation ullamco.</p>
  <p class="abs feature-copy" style="top:1996px">laboris nisi ut aliquip ex ea commodo consequat. Duis aute irure dolor in reprehenderit in voluptate velit esse cillum dolore eu.</p>
  <a class="abs btn btn-red" style="left:683px;top:2068px;width:178px;height:52px">Learn More</a>
</section>

<section>
  <div class="abs careers"></div>
  <h2 class="abs careers-title display">Careers</h2>
  <p class="abs careers-copy">Lorem ipsum dolor sit amet, consectetur adipiscing elit, sed do eiusmod tempor incididunt ut labore et dolore magna aliqua. Ut enim ad minim veniam, quis nostrud exercitation ullamco.</p>
  <a class="abs btn btn-dark" style="left:942px;top:2338px;width:177px;height:52px">Learn More</a>
</section>

<footer>
  <div class="abs footer"></div>
  <h3 class="abs footer-title display" style="left:80px">Sitemap</h3>
  <a class="abs sitemap-link" style="left:98px;top:2592px">Home</a>
  <a class="abs sitemap-link" style="left:98px;top:2631px">About us</a>
  <a class="abs sitemap-link" style="left:98px;top:2669px">Services</a>
  <a class="abs sitemap-link" style="left:276px;top:2592px">Containers</a>
  <a class="abs sitemap-link" style="left:276px;top:2631px">Career</a>
  <a class="abs sitemap-link" style="left:276px;top:2669px">Contact</a>

  <div class="abs footer-brand">
    <span class="brand-dot"></span>
    <span class="brand-name">Brandwyn Fuel</span>
  </div>

  <h3 class="abs footer-title display" style="left:846px">Contact Info</h3>
  <svg class="abs contact-icon" style="top:2596px" viewBox="0 0 24 24" aria-hidden="true"><path fill="#e3232d" d="M12 1a8 8 0 0 0-8 8c0 6 8 14 8 14s8-8 8-14a8 8 0 0 0-8-8zm0 11a3 3 0 1 1 0-6 3 3 0 0 1 0 6z"/></svg>
  <p class="abs contact-line" style="top:2588px">Lorem ipsum dolor sit amet, consect adipiscing elit, sed do eiusmod.</p>
  <svg class="abs contact-icon" style="top:2657px" viewBox="0 0 24 24" aria-hidden="true"><path fill="#e3232d" d="M6.6 10.8a15 15 0 0 0 6.6 6.6l2.2-2.2c.3-.3.7-.4 1-.2 1.1.4 2.3.6 3.6.6.6 0 1 .4 1 1V20c0 .6-.4 1-1 1A17 17 0 0 1 3 4c0-.6.4-1 1-1h3.5c.6 0 1 .4 1 1 0 1.3.2 2.5.6 3.6.1.3 0 .7-.2 1z"/></svg>
  <p class="abs contact-line" style="top:2653px">555 014 2290</p>
  <svg class="abs contact-icon" style="top:2694px" viewBox="0 0 24 24" aria-hidden="true"><path fill="#e3232d" d="M2 5h20v14H2zm2 2v.5l8 5 8-5V7l-8 5z"/></svg>
  <p class="abs contact-line" style="top:2690px">info@brandwynfuel.com</p>

  <div class="abs copyright-bar">©BRANDWYN FUEL. 2019 - All Rights Reserved.</div>
</footer>

</body>
</html>
```